1 Banner für Affiliate-Marketing (Börse/Trading)
Zielgruppe
Wir vermitteln Kunden an einen Broker. Die Kunden eröffnen Handelskonten, in denen sie selbständig Finanzprodukte (CFDs, Forex, Aktien, Edelmetalle,...) gehebelt handeln. Wir bieten dem Kunden eine Dienstleistung an, indem wir Broker vorauswählen, technischen Support liefern, bei der Kontoeröffnung unterstützen und auf Wunsch auch Trader ausbilden.
Zielgruppe: männlich, finanz- und risikoaffin, Spekulant
Aufgabenstellung
Wir benötigen 1 klickstarken Banner für das Affiliate-Marketing
Bannergröße: 300*250
Formate: GIF, PNG, JPG, Vektor
Gerne auch animierte Vorschläge, aber bitte nicht ausschließlich.
Zusätzliche Info, die verarbeitet werden kann (aber nicht muss): Kelvora Bank hat in 2016 bei 2 Kundenumfragen den Testsieg als bester Broker gewonnen.
Design ist frei und muss sich nicht an der Homepage orientieren - vielmehr suchen wir klickstarke Banner aus der Finanz-/Börsenwelt mit Bildern Ihrer Wahl.

```html
<!DOCTYPE html>
<html lang="de">
<head>
<meta charset="utf-8">
<title>Kelvora Bank – Banner 300x250</title>
<link rel="stylesheet" href="https://fonts.googleapis.com/css2?family=Lato:ital,wght@0,400;0,700;1,400;1,700&display=swap">
<style>
  :root {
    --backdrop-edge: #ececec;
    --backdrop-mid: #f7f7f7;
    --page-white: #ffffff;
    --label-grey: #a9a9a9;
    --navy: #1f2a56;
    --orange: #ff6a00;
    --highlight-bg: #1d2450;
    --highlight-text: #fff200;
    --text-white: #ffffff;
    --sky-light: #d6eefb;
    --sky-mid: #8fcdf0;
    --sky-deep: #4aa3dc;
    --floor: #e9edf0;
  }
  * { margin: 0; padding: 0; box-sizing: border-box; }
  html, body {
    width: 1200px;
    height: 1010px;
    overflow: hidden;
    background: var(--page-white);
    font-family: "Lato", Arial, sans-serif;
  }
  .stage {
    position: relative;
    width: 1200px;
    height: 1010px;
  }
  .backdrop {
    position: absolute;
    left: 0; top: 0;
    width: 1200px;
    height: 920px;
    background: radial-gradient(ellipse at 50% 50%, var(--page-white) 0%, var(--backdrop-mid) 45%, var(--backdrop-edge) 100%);
  }
  .size-label {
    position: absolute;
    top: 160px;
    left: 0;
    width: 1175px;
    text-align: center;
    font-size: 30px;
    font-weight: 700;
    font-style: italic;
    color: var(--label-grey);
    letter-spacing: 0.5px;
  }
  .banner {
    position: absolute;
    left: 320px;
    top: 273px;
    width: 569px;
    height: 474px;
    overflow: hidden;
    background: var(--page-white);
    box-shadow: 0 10px 40px rgba(0,0,0,0.12);
  }
  .banner-header {
    position: relative;
    z-index: 1;
    height: 74px;
    background: var(--page-white);
    display: flex;
    align-items: center;
    justify-content: center;
    gap: 16px;
  }
  .brand-mark {
    width: 26px;
    height: 26px;
    background: var(--orange);
  }
  .brand-name {
    font-size: 48px;
    font-weight: 700;
    font-style: normal;
    color: var(--navy);
    line-height: 1;
  }
  .banner-visual {
    position: absolute;
    left: 0; top: 74px;
    width: 569px;
    height: 400px;
    background:
      linear-gradient(180deg, rgba(255,255,255,0) 70%, var(--floor) 100%),
      linear-gradient(180deg, var(--sky-mid) 0%, var(--sky-light) 40%, var(--sky-deep) 62%, #c9d7e0 80%);
  }
  .headline {
    position: absolute;
    left: 0; top: 88px;
    width: 569px;
    text-align: center;
    font-size: 29px;
    font-style: italic;
    color: var(--navy);
    line-height: 34px;
  }
  .highlight {
    background: var(--highlight-bg);
    color: var(--highlight-text);
    font-weight: 700;
    padding: 0 6px;
  }
  .cta {
    position: absolute;
    left: 25px;
    top: 377px;
    width: 271px;
    height: 66px;
    background: var(--orange);
    color: var(--text-white);
    font-size: 29px;
    font-style: italic;
    display: flex;
    align-items: center;
    justify-content: center;
    gap: 12px;
  }
</style>
</head>
<body>
<div class="stage">
  <div class="backdrop"></div>
  <div class="size-label">300X250</div>

  <div class="banner">
    <div class="banner-visual" role="img" aria-label="Geschäftsmann im Anzug vor einem Panoramafenster mit Skyline und Börsenchart-Balken"></div>
    <div class="banner-header">
      <span class="brand-mark"></span>
      <span class="brand-name">Kelvora Bank</span>
    </div>
    <p class="headline">
      hat in 2016<br>
      bei 2 Kundenumfragen den<br>
      Testsieg <span class="highlight">als bester Broker</span><br>
      gewonnen.
    </p>
    <div class="cta">
      <span>KLICKEN HIER</span>
      <svg width="10" height="16" viewBox="0 0 10 16" aria-hidden="true"><path d="M1 1 L9 8 L1 15 Z" fill="#ffffff"/></svg>
    </div>
  </div>
</div>
</body>
</html>
```